High Tech Real Estate Startup needs a business card

We are developing an innovative real estate marketing product based around advanced search and virtual reality.

We talk to people, we need business cards.

Target Market(s)

The target market is technology professionals and realtors.

Contact Information for Business Card

The information to be included will include

Name
Title
Phone Number
E-mail Address
www.zelquin.com

It should use simple iconography for each one of those fields.

Font styles to use
Other font styles liked:
• Co, Jubilat, Avenir

Colors

Designer to choose colors to be used in the design.

Requirements
Must have
• Clean aesthetic,
• Good use of negative space.
• It should use our company logo, shown in the attached file. It is able to use the negative of that logo (coloured font and white background) and I have attached other acceptable accent colours in a swatch file.
Should not have
• Should not be too busy
• No extraneous text (slogans, tag lines etc)

```html
<!DOCTYPE html>
<html lang="en">
<head>
<meta charset="utf-8">
<title>Zelquin Business Card</title>
<link rel="stylesheet" href="https://fonts.googleapis.com/css2?family=Varela+Round&family=Roboto:wght@400&family=Roboto+Condensed:wght@400;500&display=swap">
<style>
  :root {
    --teal: #04b9bf;
    --white: #ffffff;
    --ink: #3a3a3a;
    --backdrop: #222324;
  }
  * { margin: 0; padding: 0; box-sizing: border-box; }
  html, body {
    width: 1200px; height: 960px; overflow: hidden;
    background: var(--backdrop);
  }
  .canvas { position: relative; width: 1200px; height: 960px; }

  .card {
    position: absolute; left: 320px; width: 600px; height: 342px; overflow: hidden;
  }

  /* Back of card */
  .card--back { top: 108px; background: var(--teal); }
  .card--back .brand-name {
    position: absolute; left: 0; right: 0; top: 122px;
    text-align: center; font-family: "Varela Round", sans-serif;
    font-size: 64px; letter-spacing: 2px; color: var(--white); line-height: 1;
  }
  .card--back .web-address {
    position: absolute; left: 0; right: 0; top: 260px;
    text-align: center; font-family: "Roboto", sans-serif;
    font-size: 13px; letter-spacing: 4.5px; color: var(--white);
  }

  /* Front of card */
  .card--front { top: 493px; background: var(--white); }
  .card--front .sweep { position: absolute; inset: 0; width: 600px; height: 342px; }
  .card--front .brand-name {
    position: absolute; left: 47px; top: 74px;
    font-family: "Varela Round", sans-serif; font-size: 58px;
    letter-spacing: 1px; color: var(--white); line-height: 1;
  }
  .contact {
    position: absolute; right: 32px; top: 198px; text-align: right;
  }
  .contact__name {
    font-family: "Roboto Condensed", sans-serif; font-weight: 500;
    font-size: 22px; color: var(--teal); line-height: 26px;
  }
  .contact__title {
    font-family: "Roboto Condensed", sans-serif; font-weight: 400;
    font-size: 15px; color: var(--ink); line-height: 20px;
  }
  .contact__list { list-style: none; margin-top: 13px; }
  .contact__item {
    display: flex; justify-content: flex-end; align-items: center; gap: 6px;
    font-family: "Roboto", sans-serif; font-size: 14px; color: var(--ink);
    line-height: 19.5px;
  }
  .contact__icon { width: 13px; height: 13px; fill: var(--teal); flex: none; }
</style>
</head>
<body>
<main class="canvas">

  <section class="card card--back" aria-label="Card back">
    <div class="brand-name">ZELQUIN</div>
    <div class="web-address">WWW.ZELQUIN.COM</div>
  </section>

  <section class="card card--front" aria-label="Card front">
    <svg class="sweep" viewBox="0 0 600 342" aria-hidden="true">
      <path d="M0,0 H455 C495,18 492,78 462,128 C405,218 282,290 168,342 H0 Z" fill="var(--teal)"/>
      <path d="M482,0 C518,24 512,88 478,140 C412,232 290,292 176,342" fill="none" stroke="var(--teal)" stroke-width="3"/>
    </svg>
    <div class="brand-name">ZELQUIN</div>

    <div class="contact">
      <div class="contact__name">DANA WHITLOW</div>
      <div class="contact__title">CEO/FOUNDER</div>
      <ul class="contact__list">
        <li class="contact__item">555 014 2938
          <svg class="contact__icon" viewBox="0 0 24 24" aria-hidden="true"><path d="M6.6 10.8c1.4 2.8 3.8 5.1 6.6 6.6l2.2-2.2c.3-.3.7-.4 1-.2 1.1.4 2.3.6 3.6.6.6 0 1 .4 1 1V20c0 .6-.4 1-1 1C10.6 21 3 13.4 3 4c0-.6.4-1 1-1h3.5c.6 0 1 .4 1 1 0 1.3.2 2.5.6 3.6.1.3 0 .7-.2 1z"/></svg>
        </li>
        <li class="contact__item">dana@zelquin.com
          <svg class="contact__icon" viewBox="0 0 24 24" aria-hidden="true"><path d="M2 5h20v14H2z M3.5 6.5v.6L12 13l8.5-5.9v-.6z" fill-rule="evenodd"/></svg>
        </li>
        <li class="contact__item">www.zelquin.com
          <svg class="contact__icon" viewBox="0 0 24 24" aria-hidden="true"><circle cx="12" cy="12" r="10"/><path d="M8 6c2 1 3 3 2 5s-3 2-3 4M15 5c-1 2 0 3 2 4s2 3 1 5" stroke="#fff" stroke-width="1.6" fill="none"/></svg>
        </li>
      </ul>
    </div>
  </section>

</main>
</body>
</html>
```